Business Card for a Jewellery Brand

Business card for an upscale jewellery brand. Attached is the brand logo and icon and color board. I am looking for two card versions: one for the founder and one is generic. The card should be elegant and convey upscale and premium feel. I am open to both square and rectangle card shapes.

Industry/Entity Type

Jewelry

Contact Information for Business Card

Two cards: (1) Sunela Parvaniya (Founder) (2) General
(1) Sunela Parvaniya card should have Name: Sunela Parvaniya, Title: Founder Email id: sunela@quiremo.com.au. Phone no: +61452913307
(2) Generic card should have Email id: info@quiremo.com.au. Phone no: +61436207518

Requirements
Must have
• Workmark
• ICON
• Phone no
• Email ID
• ABN: 58219740312 (Note: ABN is Business number in Australia)
• Website: www.quiremo.com.au
• Instagram: quiremo_jewellery
• Facebook: @quiremojewellery
Nice to have
• Tagline

```html
<!DOCTYPE html>
<html lang="en">
<head>
<meta charset="utf-8">
<title>Quiremo Business Cards</title>
<link rel="stylesheet" href="https://fonts.googleapis.com/css2?family=Open+Sans:wght@400;600;700&display=swap">
<style>
  :root {
    --backdrop: #2b2b2c;
    --card: #141414;
    --rose: #ea9a8f;
    --ink: #f1f1f1;
  }
  * { box-sizing: border-box; margin: 0; padding: 0; }
  html, body {
    width: 1200px;
    height: 900px;
    overflow: hidden;
    background: var(--backdrop);
    font-family: "Open Sans", Arial, sans-serif;
  }
  .stage {
    position: relative;
    width: 1200px;
    height: 900px;
  }
  .card {
    position: absolute;
    top: 310px;
    width: 525px;
    height: 300px;
    background: var(--card);
    border-radius: 22px;
  }
  .card--front { left: 50px; }
  .card--back { left: 625px; }

  /* Front */
  .front-mark {
    position: absolute;
    left: 0;
    top: 0;
    width: 262px;
    height: 300px;
    display: flex;
    align-items: center;
    justify-content: center;
  }
  .wordmark {
    color: var(--rose);
    font-weight: 400;
    letter-spacing: 0.32em;
    line-height: 1;
  }
  .front-mark .wordmark { font-size: 30px; }

  .details {
    position: absolute;
    left: 285px;
    top: 52px;
    color: var(--ink);
  }
  .details__name {
    color: var(--rose);
    font-weight: 700;
    font-size: 18px;
    line-height: 1.2;
  }
  .details__title {
    font-size: 14px;
    line-height: 1.3;
  }
  .details__abn {
    margin-top: 14px;
    font-size: 14px;
  }
  .details__abn b {
    color: var(--rose);
    font-weight: 700;
  }
  .contact-list {
    list-style: none;
    margin-top: 12px;
    padding-left: 16px;
  }
  .contact-list li {
    display: flex;
    align-items: center;
    gap: 10px;
    font-size: 14px;
    line-height: 22px;
  }
  .contact-list svg {
    width: 11px;
    height: 11px;
    flex: none;
    fill: var(--ink);
  }

  /* Back */
  .back-brand {
    position: absolute;
    inset: 0;
    display: flex;
    flex-direction: column;
    align-items: center;
    justify-content: center;
    gap: 22px;
  }
  .back-brand__square {
    width: 40px;
    height: 40px;
    border: 3px solid var(--rose);
  }
  .back-brand .wordmark { font-size: 42px; padding-left: 0.32em; }
</style>
</head>
<body>
<main class="stage">

  <section class="card card--front" aria-label="Founder card, front">
    <div class="front-mark">
      <span class="wordmark">QUIREMO</span>
    </div>
    <div class="details">
      <p class="details__name">Sunela Parvaniya</p>
      <p class="details__title">Founder</p>
      <p class="details__abn"><b>ABN:</b> 58219740312</p>
      <ul class="contact-list">
        <li>
          <svg viewBox="0 0 12 12" aria-hidden="true"><path d="M2.5 0.5l2 2.2-1 1.4c.8 1.6 2 2.8 3.6 3.6l1.4-1 2.2 2-1.2 2.3C5 10.8 1.2 7 .3 1.7z"/></svg>
          +61452913307
        </li>
        <li>
          <svg viewBox="0 0 12 12" aria-hidden="true"><path d="M0 2h12v8H0z M0.8 2.6 6 6.6l5.2-4H0.8z" fill-rule="evenodd"/></svg>
          sunela@quiremo.com.au
        </li>
        <li>
          <svg viewBox="0 0 12 12" aria-hidden="true"><circle cx="6" cy="6" r="5.5"/></svg>
          www.quiremo.com.au
        </li>
        <li>
          <svg viewBox="0 0 12 12" aria-hidden="true"><rect x="0.5" y="0.5" width="11" height="11" rx="2"/></svg>
          quiremo_jewellery
        </li>
        <li>
          <svg viewBox="0 0 12 12" aria-hidden="true"><circle cx="6" cy="6" r="5.5"/></svg>
          @quiremojewellery
        </li>
      </ul>
    </div>
  </section>

  <section class="card card--back" aria-label="Card back">
    <div class="back-brand">
      <span class="back-brand__square" aria-hidden="true"></span>
      <span class="wordmark">QUIREMO</span>
    </div>
  </section>

</main>
</body>
</html>
```